Industrial Company-Pop-Up Banner Design for Demolition and Infrastructure Company

Hi-
We need to create 2 pop-up banners for our company. They will both have the same logo, but different photos. We would like to have the colors white, red, and black and feature a modern design. I have attached some inspiration photos.

Target Market(s)

Trade Show/Job Fair Audience

Industry/Entity Type

construction, industrial

Font styles to use
Sans Serif

Colors
EB3D1F
EC4F4E
F09395
F8D3D4
FCEDEE

Requirements
Must have
• 2 versions, each with different photos but same design. Logo, Red, Black, and White Color Scheme, Modern Design
Nice to have
• Modern Design similar to the inspiration photos

```html
<!DOCTYPE html>
<html lang="en">
<head>
<meta charset="utf-8">
<title>Holloway Works – Pop-Up Banners</title>
<link rel="stylesheet" href="https://fonts.googleapis.com/css2?family=Poppins:wght@400;700;800&family=Oswald:wght@600&display=swap">
<style>
  :root {
    --red: #d71f26;
    --black: #1d1d1d;
    --white: #ffffff;
    --page: #ffffff;
  }
  * { margin: 0; padding: 0; box-sizing: border-box; }
  html, body {
    width: 760px;
    height: 1200px;
    overflow: hidden;
    background: var(--page);
  }
  .banner-pair {
    display: flex;
    justify-content: center;
    gap: 34px;
    padding-top: 192px;
  }
  .banner {
    width: 340px;
    height: 815px;
    display: block;
    box-shadow: 0 6px 14px rgba(0,0,0,0.28);
  }
  .brand-name {
    font-family: "Poppins", sans-serif;
    font-weight: 700;
    font-size: 38px;
    fill: var(--white);
    letter-spacing: 1px;
  }
  .brand-mark { fill: var(--red); }
  .headline-top {
    font-family: "Poppins", sans-serif;
    font-weight: 800;
    font-size: 58px;
    fill: var(--red);
  }
  .headline-mid {
    font-family: "Poppins", sans-serif;
    font-weight: 800;
    font-size: 51px;
    fill: var(--black);
  }
  .headline-main {
    font-family: "Oswald", sans-serif;
    font-weight: 600;
    font-size: 112px;
    fill: var(--red);
  }
  .since-bar { fill: var(--black); }
  .since-text {
    font-family: "Poppins", sans-serif;
    font-size: 27px;
    fill: var(--white);
    letter-spacing: 9px;
  }
  .since-year { font-weight: 800; }
  .web {
    font-family: "Poppins", sans-serif;
    font-size: 19px;
    letter-spacing: 5px;
    fill: var(--black);
  }
  .web-accent { fill: var(--red); font-weight: 700; }
  .panel-top { fill: var(--black); }
  .panel-base { fill: var(--white); }
  .divider { stroke: var(--black); stroke-width: 6; fill: none; }
  .frame-dark { stroke: #2b2b2b; stroke-width: 9; }
  .frame-red { stroke: var(--red); stroke-width: 8; }
  .accent-diamond { fill: var(--red); }
</style>
</head>
<body>
<main class="banner-pair">

  <!-- Version one -->
  <svg class="banner" viewBox="0 0 470 1127" aria-label="Pop-up banner, version one">
    <defs>
      <linearGradient id="grey-a" x1="0" y1="0" x2="0.3" y2="1">
        <stop offset="0" stop-color="#f0f0f0"/><stop offset="0.35" stop-color="#b4b4b4"/><stop offset="0.7" stop-color="#6e6e6e"/><stop offset="1" stop-color="#9a9a9a"/>
      </linearGradient>
      <linearGradient id="red-a" x1="0" y1="0" x2="0" y2="1">
        <stop offset="0" stop-color="#c81a20"/><stop offset="0.5" stop-color="#9e1016"/><stop offset="1" stop-color="#d3232a"/>
      </linearGradient>
      <linearGradient id="mid-a" x1="0" y1="0" x2="0" y2="1">
        <stop offset="0" stop-color="#dbe7f1"/><stop offset="0.5" stop-color="#8aa9c6"/><stop offset="0.75" stop-color="#b9bcbf"/><stop offset="1" stop-color="#6f7d58"/>
      </linearGradient>
      <linearGradient id="low-a" x1="0" y1="0" x2="0" y2="1">
        <stop offset="0" stop-color="#b8cbe0"/><stop offset="0.35" stop-color="#607f38"/><stop offset="0.6" stop-color="#d9b22c"/><stop offset="1" stop-color="#b96a40"/>
      </linearGradient>
    </defs>
    <polygon role="img" aria-label="Black and white photo of an excavator demolishing a brewery building" fill="url(#grey-a)" points="0,60 245,295 245,585 0,825"/>
    <polygon role="img" aria-label="Red-toned photo of an industrial plant structure" fill="url(#red-a)" points="470,80 245,295 245,585 470,800"/>
    <polygon class="panel-top" points="0,0 470,0 470,80 245,295 0,60"/>
    <polygon role="img" aria-label="Photo of a power plant smokestack implosion" class="frame-dark" fill="url(#mid-a)" points="241,300 381,440 241,580 101,440"/>
    <polygon class="panel-base" points="0,825 245,583 470,800 470,1127 0,1127"/>
    <polyline class="divider" points="0,825 245,583 470,800"/>
    <polygon class="accent-diamond" points="144,700 179,735 144,770 109,735"/>
    <polygon class="accent-diamond" points="349,700 384,735 349,770 314,735"/>
    <polygon role="img" aria-label="Photo of yellow articulated haul trucks on a dirt site" class="frame-red" fill="url(#low-a)" points="243,600 333,690 243,780 153,690"/>
    <rect class="brand-mark" x="110" y="96" width="26" height="26"/>
    <text class="brand-name" x="255" y="122" text-anchor="middle">HOLLOWAY</text>
    <text class="brand-name" x="235" y="168" text-anchor="middle">WORKS</text>
    <text class="headline-top" x="235" y="865" text-anchor="middle">SHAPING</text>
    <text class="headline-mid" x="235" y="917" text-anchor="middle">AMERICA’S</text>
    <text class="headline-main" x="235" y="1012" text-anchor="middle" textLength="318" lengthAdjust="spacingAndGlyphs">SKYLINE</text>
    <rect class="since-bar" x="77" y="1020" width="317" height="35"/>
    <text class="since-text" x="238" y="1048" text-anchor="middle">SINCE <tspan class="since-year">1959</tspan></text>
    <text class="web" x="235" y="1096" text-anchor="middle">www.<tspan class="web-accent">hollowayworks</tspan>.com</text>
  </svg>

  <!-- Version two -->
  <svg class="banner" viewBox="0 0 470 1127" aria-label="Pop-up banner, version two">
    <defs>
      <linearGradient id="grey-b" x1="0" y1="0" x2="0.3" y2="1">
        <stop offset="0" stop-color="#f4f4f4"/><stop offset="0.3" stop-color="#9c9c9c"/><stop offset="0.65" stop-color="#c4c4c4"/><stop offset="1" stop-color="#858585"/>
      </linearGradient>
      <linearGradient id="red-b" x1="0" y1="0" x2="0" y2="1">
        <stop offset="0" stop-color="#e0292f"/><stop offset="0.5" stop-color="#b8161d"/><stop offset="1" stop-color="#8f1016"/>
      </linearGradient>
      <linearGradient id="mid-b" x1="0" y1="0" x2="0" y2="1">
        <stop offset="0" stop-color="#34649a"/><stop offset="0.45" stop-color="#c9ccd0"/><stop offset="0.72" stop-color="#d8b524"/><stop offset="1" stop-color="#8a8a80"/>
      </linearGradient>
      <linearGradient id="low-b" x1="0" y1="0" x2="0" y2="1">
        <stop offset="0" stop-color="#adc4da"/><stop offset="0.35" stop-color="#5e7d36"/><stop offset="0.6" stop-color="#e0b72a"/><stop offset="1" stop-color="#c0703e"/>
      </linearGradient>
    </defs>
    <polygon role="img" aria-label="Black and white photo of an excavator clearing a rubble site" fill="url(#grey-b)" points="0,60 245,295 245,585 0,825"/>
    <polygon role="img" aria-label="Red-toned photo of a refinery tower being dismantled" fill="url(#red-b)" points="470,80 245,295 245,585 470,800"/>
    <polygon class="panel-top" points="0,0 470,0 470,80 245,295 0,60"/>
    <polygon role="img" aria-label="Photo of a yellow excavator in front of a large assembly building" class="frame-dark" fill="url(#mid-b)" points="241,300 381,440 241,580 101,440"/>
    <polygon class="panel-base" points="0,825 245,583 470,800 470,1127 0,1127"/>
    <polyline class="divider" points="0,825 245,583 470,800"/>
    <polygon class="accent-diamond" points="144,700 179,735 144,770 109,735"/>
    <polygon class="accent-diamond" points="349,700 384,735 349,770 314,735"/>
    <polygon role="img" aria-label="Photo of a yellow excavator loading a truck with red earth" class="frame-red" fill="url(#low-b)" points="243,600 333,690 243,780 153,690"/>
    <rect class="brand-mark" x="110" y="96" width="26" height="26"/>
    <text class="brand-name" x="255" y="122" text-anchor="middle">HOLLOWAY</text>
    <text class="brand-name" x="235" y="168" text-anchor="middle">WORKS</text>
    <text class="headline-top" x="235" y="865" text-anchor="middle">SHAPING</text>
    <text class="headline-mid" x="235" y="917" text-anchor="middle">AMERICA’S</text>
    <text class="headline-main" x="235" y="1012" text-anchor="middle" textLength="318" lengthAdjust="spacingAndGlyphs">SKYLINE</text>
    <rect class="since-bar" x="77" y="1020" width="317" height="35"/>
    <text class="since-text" x="238" y="1048" text-anchor="middle">SINCE <tspan class="since-year">1959</tspan></text>
    <text class="web" x="235" y="1096" text-anchor="middle">www.<tspan class="web-accent">hollowayworks</tspan>.com</text>
  </svg>

</main>
</body>
</html>
```